TALMORK

The business want a professional looking business card. We have a scetch we will add but want the extra upgrade, and would like more suggestions for variations of our business cards.

```html
<!DOCTYPE html>
<html lang="en">
<head>
<meta charset="utf-8">
<title>TALMORK Business Card</title>
<link href="https://fonts.googleapis.com/css2?family=Montserrat:wght@400;500;700&display=swap" rel="stylesheet">
<style>
  :root {
    --bg: #1b1b1b;
    --card: #252525;
    --card-back: #1f1f1f;
    --gold: #d6ab52;
    --gold-light: #f1cd72;
    --gold-dark: #a57a2c;
    --white: #f2f2f2;
    --pattern-dark: #1a1a1a;
    --pattern-light: #5a5a5a;
  }
  * { margin: 0; padding: 0; box-sizing: border-box; }
  html, body { width: 1200px; height: 1059px; overflow: hidden; }
  body {
    background: var(--bg);
    font-family: "Montserrat", sans-serif;
    position: relative;
  }
  .card {
    position: absolute;
    border-radius: 24px;
    overflow: hidden;
    box-shadow: 0 14px 30px rgba(0,0,0,.55);
  }
  .card-front {
    left: 257px; top: 89px; width: 687px; height: 390px;
    background: var(--card);
  }
  .gold-band {
    position: absolute; left: 0; bottom: 0; width: 100%; height: 17px;
    background: linear-gradient(90deg, var(--gold-light), var(--gold-dark));
  }
  .brand {
    position: absolute; left: 176px; top: 120px; width: 0;
    display: flex; flex-direction: column; align-items: center;
  }
  .brand-dot {
    width: 44px; height: 44px; border-radius: 50%;
    background: var(--gold); margin-bottom: 30px;
  }
  .brand-name {
    color: var(--gold); font-weight: 500; font-size: 26px;
    letter-spacing: 8px; white-space: nowrap; padding-left: 8px;
  }
  .brand-tagline {
    color: var(--gold); font-size: 8px; font-weight: 500;
    letter-spacing: 4.5px; white-space: nowrap; margin-top: 8px; padding-left: 4px;
  }
  .divider {
    position: absolute; left: 307px; top: 113px; width: 1px; height: 166px;
    background: var(--gold-dark);
  }
  .person { position: absolute; left: 344px; top: 108px; }
  .person-name { color: var(--gold); font-weight: 700; font-size: 24px; line-height: 1.2; }
  .person-title { color: var(--white); font-size: 19px; line-height: 1.3; }
  .contacts { position: absolute; left: 344px; top: 187px; list-style: none; }
  .contact {
    display: flex; align-items: center; gap: 10px;
    color: var(--white); font-size: 19px; height: 33.5px;
  }
  .contact svg { width: 16px; height: 16px; flex: none; }
  .card-back {
    left: 254px; top: 546px; width: 693px; height: 394px;
    background: var(--card-back);
  }
  .pattern {
    position: absolute; inset: 0;
    background: linear-gradient(120deg, var(--pattern-dark) 35%, #333 60%, var(--pattern-light) 100%);
    opacity: .55;
  }
  .back-brand {
    position: absolute; left: 544px; top: 254px; width: 0;
    display: flex; flex-direction: column; align-items: center;
  }
  .back-brand .brand-dot { width: 40px; height: 40px; margin-bottom: 12px; }
  .back-brand .brand-name { font-size: 22px; letter-spacing: 6px; padding-left: 6px; }
  .back-brand .brand-tagline { font-size: 7px; letter-spacing: 4px; margin-top: 6px; }
</style>
</head>
<body>
  <section class="card card-front">
    <div class="brand">
      <div class="brand-dot"></div>
      <div class="brand-name">TALMORK</div>
      <div class="brand-tagline">SINCE 2026</div>
    </div>
    <div class="divider"></div>
    <div class="person">
      <div class="person-name">Arne Lukas Holmvik</div>
      <div class="person-title">CEO &amp; Founder</div>
    </div>
    <ul class="contacts">
      <li class="contact">
        <svg viewBox="0 0 16 16"><path fill="#d6ab52" d="M3 1.5l2.5-.5 1.5 3.5-1.7 1.2a8 8 0 004.5 4.5L11 8.5l3.5 1.5-.5 2.5c-.3 1.2-1.5 2-2.7 1.8C6.3 13.5 2.5 9.7 1.7 4.2 1.5 3 2 1.8 3 1.5z"/></svg>
        004791234567
      </li>
      <li class="contact">
        <svg viewBox="0 0 16 16"><path fill="#d6ab52" d="M1 6l7-5 7 5v8H1z"/><path fill="#252525" d="M2 7l6 4 6-4v6H2z" opacity=".5"/></svg>
        talmork.llc@mailhub.com
      </li>
      <li class="contact">
        <svg viewBox="0 0 16 16"><circle cx="8" cy="8" r="7" fill="#d6ab52"/><path fill="#252525" opacity=".45" d="M5 3c2 1 1 3 3 3s1 3-1 3-2 2-1 4C3 12 2 9 3 6z"/></svg>
        www.talmork.llc
      </li>
    </ul>
    <div class="gold-band"></div>
  </section>

  <section class="card card-back">
    <div class="pattern" role="img" aria-label="Repeating tonal pattern of decorative floral motifs, fading from black to grey"></div>
    <div class="back-brand">
      <div class="brand-dot"></div>
      <div class="brand-name">TALMORK</div>
      <div class="brand-tagline">SINCE 2026</div>
    </div>
  </section>
</body>
</html>
```